Need to drive pregnant women to my 3d4d ultrasound studio where i provide 4d ultrasound with hyperalistic imaging and gender reveals

Industry/Entity Type

Healthcare

Font styles to use
Decorative
Script

Requirements
Must have
• My Company name Cielo de Nuestra Espera 4D. EVERYTHING HAS TO BE IN SPANISH
Nice to have
• SIMPLE AND NOT TOO BUSY
Should not have
• website

```html
<!DOCTYPE html>
<html lang="es">
<head>
<meta charset="utf-8">
<title>Cielo de Nuestra Espera 4D — Banner</title>
<link href="https://fonts.googleapis.com/css2?family=Dancing+Script:wght@700&family=Roboto:wght@700&display=swap" rel="stylesheet">
<style>
  :root {
    --backdrop: #a0a0a0;
    --paper: #ffffff;
    --ink: #000000;
    --ink-soft: #111111;
    --sheen: #5c5c5e;
    --silver-dark: #7a7a7a;
    --silver-light: #f0f0f0;
    --amber-dark: #6b2e05;
    --amber: #c8701f;
    --amber-light: #e9a14d;
    --skin-dark: #b98376;
    --skin: #e6b9aa;
    --skin-light: #f4d8cc;
  }
  html, body {
    margin: 0;
    padding: 0;
    width: 1200px;
    height: 600px;
    overflow: hidden;
    background: var(--backdrop);
  }
  .canvas {
    position: relative;
    width: 1200px;
    height: 600px;
    font-family: "Roboto", Arial, sans-serif;
  }
  .banner-shapes {
    position: absolute;
    inset: 0;
    width: 1200px;
    height: 600px;
  }
  .brand-title {
    position: absolute;
    left: 137px;
    top: 186px;
    margin: 0;
    color: var(--paper);
    font-family: "Roboto", Arial, sans-serif;
    font-weight: 700;
    font-size: 45px;
    line-height: 57px;
    text-transform: uppercase;
    letter-spacing: 0.3px;
  }
  .tagline {
    position: absolute;
    left: 136px;
    top: 344px;
    width: 470px;
    margin: 0;
    color: var(--ink);
    font-family: "Dancing Script", "Brush Script MT", cursive;
    font-weight: 700;
    font-size: 38px;
    line-height: 42px;
  }
  .photo {
    position: absolute;
    top: 196px;
    width: 169px;
    height: 223px;
  }
  .photo--scan {
    left: 740px;
    background: radial-gradient(ellipse at 45% 45%, var(--amber-light) 0%, var(--amber) 45%, var(--amber-dark) 100%);
  }
  .photo--newborn {
    left: 913px;
    background: radial-gradient(ellipse at 45% 55%, var(--skin-light) 0%, var(--skin) 55%, var(--skin-dark) 100%);
  }
</style>
</head>
<body>
<div class="canvas">
  <svg class="banner-shapes" viewBox="0 0 2000 1000" aria-hidden="true">
    <defs>
      <linearGradient id="header-sheen" x1="0" y1="0" x2="1" y2="0">
        <stop offset="0" stop-color="var(--ink)"/>
        <stop offset="0.2" stop-color="var(--ink-soft)"/>
        <stop offset="0.4" stop-color="var(--sheen)"/>
        <stop offset="0.6" stop-color="var(--ink-soft)"/>
        <stop offset="1" stop-color="var(--ink)"/>
      </linearGradient>
      <linearGradient id="silver-wedge" x1="0" y1="0" x2="0" y2="1">
        <stop offset="0" stop-color="var(--silver-dark)"/>
        <stop offset="0.5" stop-color="var(--silver-light)"/>
        <stop offset="1" stop-color="var(--silver-dark)"/>
      </linearGradient>
    </defs>
    <rect class="banner-card" x="131" y="256" width="1739" height="506" fill="var(--paper)"/>
    <polygon class="header-band" points="131,256 1016,256 1142,762 1120,762 1060,538 131,538" fill="url(#header-sheen)"/>
    <polygon class="silver-wedge" points="1030,256 1192,256 1090,510" fill="url(#silver-wedge)"/>
  </svg>

  <h1 class="brand-title">Cielo de Nuestra<br>Espera 4D</h1>
  <p class="tagline">Ecografía 4D hiperrealista<br>y revelación de sexo</p>

  <div class="photo photo--scan" role="img" aria-label="Imagen de ecografía 4D en tonos ámbar de un bebé en el vientre"></div>
  <div class="photo photo--newborn" role="img" aria-label="Fotografía de un recién nacido dormido"></div>
</div>
</body>
</html>
```